Advertising agency needs site design

You will be designing a clean (plenty of white space) and vivid (colorful) design that is for an advertising agency named Pixel Harbor. Their current web site is located at www.PixelHarbor.net. From there you can see their services and get a feel for the company as the site stands today.
The following are direct quotes from the client:
“I want a clean look with colors of the teal blue, deep yellow (in logo) and then a good energetic orange (deep orange - rich) should bring a good feel and enthusiasm.”
“The orange can be a nice accent color, not dominant.”
“Saw two other things I like - the website lanternfoxstudio.com was pretty cool. I liked how the top banner changed colors as you moved to different tabs. I am somewhat wanting the colors I mentioned - like the blue color we use can be lighter as long as it works with the logo. - love the tidal frames site. I want quirky, creative and clean look - fun feel but slightly sophisticated to work with the medical field.”
Pixel Harbor currently focuses on the following primary industries:
• Medical / Health Care – Currently the primary industry
• Retail Industry
• Automotive Industry
• Entertainment Industry
Primary Services
• Media Planning & Buying: Web, TV, Print, Radio
• Campaign monitoring and reporting
• Commercial Production: TV & Radio
• Strategic Planning
• Market Research
• Internet Marketing: Email, SEO, Web design / development
Primary Navigation will consist of the following:
• Home
• About Us
o History
o Principal Profile (sub nav)
o Sales Team & Partners
• Clients
• Services
• Testimonials
• Contact Us
They want the web site to act as a basis for future marketing collateral so the overall feel from the web site must be capable of translating to print and other collateral. I do not currently have a clean digital version of their logo however their logo is on the web site (pixelharbor.net)
Target Market(s)
larger companies that are purchasing air time on television and radio. Typically in the health care industry and others described above in brief.
Industry/Entity Type
Advertising
Look and feel

```html
<!DOCTYPE html>
<html lang="en">
<head>
<meta charset="utf-8">
<title>Pixel Harbor</title>
<link href="https://fonts.googleapis.com/css2?family=Arimo:wght@400;700&family=Quicksand:wght@500&display=swap" rel="stylesheet">
<style>
:root{
  --teal:#1f6f8b;
  --teal-light:#1aa3b3;
  --green:#6ab42a;
  --orange:#e04a10;
  --orange-band:#e8902a;
  --purple:#7a3b98;
  --accent:#c8641c;
  --text:#555;
  --heading:#444;
  --navy:#0e3a52;
  --navy-dark:#0a2d40;
  --panel:#ecebf0;
}
*{margin:0;padding:0;box-sizing:border-box}
html,body{width:963px;height:1200px;overflow:hidden}
body{position:relative;background:#f4f4f4;font-family:Arimo,Arial,sans-serif;color:var(--text)}
.abs{position:absolute}
.header{left:0;top:0;width:963px;height:103px;background:linear-gradient(#ffffff,#efefef)}
.logo{left:62px;top:34px;font-family:Quicksand,sans-serif;font-size:34px;font-weight:500;color:var(--teal);letter-spacing:1px;display:flex;align-items:center;gap:10px}
.logo-dot{width:14px;height:14px;border-radius:50%;background:#e8a91c}
.account{right:50px;top:13px;font-size:11px;color:#e8902a;letter-spacing:.5px}
.account span{color:#ccc;margin:0 6px}
.call{left:657px;top:42px;width:218px;height:48px;background:#fff;border:1px solid #ddd;border-radius:4px;box-shadow:0 2px 3px rgba(0,0,0,.1)}
.call-agent{left:4px;top:-20px;width:48px;height:64px;background:linear-gradient(#d6722c,#1b4a66);border-radius:24px 24px 4px 4px}
.call-label{left:76px;top:8px;font-size:12px;font-weight:700;color:var(--teal)}
.call-number{left:76px;top:22px;font-size:20px;font-weight:700;color:var(--teal)}
.nav{left:0;top:103px;width:963px;height:33px;background:linear-gradient(#ffffff,#ececec);border-top:1px solid #ddd;border-bottom:1px solid #ddd}
.nav ul{list-style:none;display:flex;position:absolute;left:44px;top:0;height:31px}
.nav li{padding:0 20px;line-height:31px;font-size:13px;color:var(--teal);border-right:1px solid #ddd}
.search{left:706px;top:108px;width:195px;height:23px;background:#fff;border:1px solid #ccc;font-size:11px;color:#999;padding:5px 8px}
.search svg{position:absolute;right:6px;top:4px}
.band{left:0;top:136px;width:963px;height:295px;background:linear-gradient(90deg,#d97b1a,#f2a640 50%,#d97b1a)}
.main{left:43px;top:146px;width:877px;height:812px;background:#fff;box-shadow:0 0 6px rgba(0,0,0,.15)}
.banner{left:47px;top:151px;width:870px;height:280px;background:linear-gradient(90deg,#3a1c08,#8a4a12 40%,#c98a2c 70%,#4a2608)}
.dots{left:88px;top:407px;display:flex;gap:6px}
.dots i{width:14px;height:14px;border-radius:50%;background:#ddd;display:block}
.dots i.on{background:#f0a030}
.industry{top:448px;width:207px;height:40px;border-radius:4px;color:#fff;font-size:16px;padding:10px 12px}
.industry svg{position:absolute;right:6px;top:4px}
.health{left:53px;background:var(--teal-light)}
.retail{left:270px;background:var(--green)}
.auto{left:486px;background:var(--orange)}
.fun{left:703px;background:var(--purple)}
h2{font-weight:400;font-size:18px;color:var(--heading)}
h2 em{font-style:normal;color:var(--accent)}
.welcome{left:62px;top:508px;width:570px}
.welcome p{margin-top:10px;font-size:11px;line-height:19.5px;color:#666;text-align:justify;letter-spacing:.6px}
.services{left:659px;top:508px;width:252px}
.services h2{color:#888}
.services ul{list-style:none;margin-top:10px}
.services li{height:24px;margin-bottom:2.5px;background:var(--panel);font-size:12px;line-height:24px;padding-left:28px;position:relative;color:#555}
.services li::before{content:"";position:absolute;left:10px;top:8px;border-left:5px solid var(--accent);border-top:4px solid transparent;border-bottom:4px solid transparent}
.news{left:73px;top:716px;width:225px}
.news-item{border-bottom:1px dashed #bbb;padding:8px 0 6px;font-size:11px;line-height:16px;color:#444}
.news-item b{display:block;color:var(--teal);font-size:11px;letter-spacing:.5px}
.news-item:last-of-type{border-bottom:none}
.more{left:217px;top:934px;font-size:10px;font-weight:700;color:#e8a010}
.testimonials{left:375px;top:716px;width:240px}
.bubble{left:369px;top:749px;width:218px;height:134px;background:#f4f4f6;border:1px solid #ddd;border-radius:18px;padding:14px 14px 0 26px;font-size:11px;line-height:15.5px;color:#666}
.bubble::before{content:"\201C";position:absolute;left:10px;top:8px;font-size:24px;color:#333}
.tail{left:400px;top:880px}
.pager{font-size:12px;font-weight:700;color:#333}
.person{left:381px;top:906px;font-size:11px;line-height:20px;color:var(--accent)}
.person b{color:var(--teal);font-style:italic}
.newsletter{left:667px;top:716px;width:222px}
.email{left:666px;top:775px;width:221px;height:26px;border:1px solid #bbb;border-radius:4px;font-size:11px;color:#aaa;padding:6px 10px}
.submit{left:802px;top:809px;width:85px;height:26px;border-radius:4px;background:#333;color:#fff;font-size:13px;font-weight:700;text-align:center;line-height:26px;letter-spacing:1px}
.clients-title{left:668px;top:832px}
.clients{left:680px;top:868px;width:194px;height:58px;background:#f4f4f6;border-radius:6px;font-size:16px;font-weight:700;color:#333;text-align:center;line-height:24px;padding-top:5px;letter-spacing:1px}
.footer{left:0;top:958px;width:963px;height:242px;background:var(--navy)}
.footer h3{font-size:12px;font-weight:700;color:#fff;letter-spacing:1px}
.footer ul{list-style:none;margin-top:15px}
.footer li{font-size:11px;line-height:21px;color:#dfe8ee;padding-left:12px;position:relative}
.footer li::before{content:"";position:absolute;left:0;top:9px;width:4px;height:4px;border-radius:50%;background:#fff}
.col{top:20px}
.social li{padding-right:30px}
.social li span{position:absolute;right:0;top:5px;width:11px;height:11px;border-radius:2px}
.contact p{font-size:11px;line-height:17px;color:#dfe8ee;margin-top:15px}
.contact .line{display:flex;align-items:center;gap:14px;margin-top:6px;font-size:11px;color:#dfe8ee;padding-left:4px}
.copy{left:0;top:1155px;width:963px;height:45px;background:var(--navy-dark);border-top:1px solid #1f4a62;text-align:center;line-height:40px;font-size:11px;color:#cfd9e0;letter-spacing:.5px}
</style>
</head>
<body>
<header class="header abs">
  <div class="logo abs"><span>pixel harbor</span><span class="logo-dot"></span></div>
  <div class="account abs">LOGIN<span>|</span>SIGN UP</div>
  <div class="call abs">
    <div class="call-agent abs" role="img" aria-label="Illustrated support agent with headset"></div>
    <div class="call-label abs">CALL US</div>
    <div class="call-number abs">555 018 2040</div>
  </div>
</header>
<nav class="nav abs">
  <ul><li>Home</li><li>About Us</li><li>Clients</li><li>Services</li><li>Testimonials</li><li>Contact Us</li></ul>
</nav>
<div class="search abs">Search
  <svg width="14" height="14" viewBox="0 0 14 14"><circle cx="6" cy="6" r="4.2" fill="none" stroke="#1f6f8b" stroke-width="2"/><line x1="9" y1="9" x2="13" y2="13" stroke="#1f6f8b" stroke-width="2.2"/></svg>
</div>
<div class="band abs"></div>
<main class="main abs"></main>
<div class="banner abs" role="img" aria-label="Banner photo of a smiling businessman surrounded by handwritten words: Automotive, Strategic Planning, Medical, Retail, Web design, Internet Marketing, Entertainment, Reporting"></div>
<div class="dots abs"><i class="on"></i><i></i><i></i><i></i></div>

<div class="industry health abs">Medical / Health<svg width="34" height="32" viewBox="0 0 34 32"><path d="M4 30 C18 28 12 4 30 2" fill="none" stroke="#fff" stroke-width="1.5"/><text x="24" y="28" fill="#fff" font-size="10">+</text></svg></div>
<div class="industry retail abs">Retail<svg width="34" height="32" viewBox="0 0 34 32"><path d="M4 30 C18 28 12 4 30 2" fill="none" stroke="#fff" stroke-width="1.5"/><text x="24" y="28" fill="#fff" font-size="10">+</text></svg></div>
<div class="industry auto abs">Automotive<svg width="34" height="32" viewBox="0 0 34 32"><path d="M4 30 C18 28 12 4 30 2" fill="none" stroke="#fff" stroke-width="1.5"/><text x="24" y="28" fill="#fff" font-size="10">+</text></svg></div>
<div class="industry fun abs">Entertainment<svg width="34" height="32" viewBox="0 0 34 32"><path d="M4 30 C18 28 12 4 30 2" fill="none" stroke="#fff" stroke-width="1.5"/><text x="24" y="28" fill="#fff" font-size="10">+</text></svg></div>

<section class="welcome abs">
  <h2>Welcome to <em>pixel harbor</em></h2>
  <p>Lorem ipsum dolor sit amet, consectetuer adipiscing elit. Aenean commodo ligula eget dolor. Aenean massa. Cum sociis natoque penatibus et magnis dis parturient montes, nascetur ridiculus mus. Donec quam felis, ultricies nec, pellentesque eu, pretium quis, sem. Nulla consequat massa quis enim. Donec pede justo, fringilla vel, aliquet nec, vulputate eget, arcu.Lorem ipsum dolor sit amet, consectetuer adipiscing elit. Aenean commodo ligula eget dolor. Aenean massa. Cum sociis natoque gnis dis parturient montes, nascetur ridiculus mus. Donec quam felis, ultricies nec, pellentesque eu, pretium quis, sem. Nulla consequat massa quis enim. Donec pede justo, fringilla vel, aliquet nec, vulputate eget, arcu.n commodo ligula eget dolor. Aenean massa.</p>
</section>

<section class="services abs">
  <h2>Services</h2>
  <ul>
    <li>Media Planning &amp; Buying</li>
    <li>Campaign monitoring and reporting</li>
    <li>Commercial Production</li>
    <li>Strategic Planning</li>
    <li>Market Research</li>
    <li>Internet Marketing</li>
  </ul>
</section>

<section class="news abs">
  <h2>News</h2>
  <div class="news-item"><b>MAY 19, 2011</b>Lorem ipsum dolor sit ametconsectetuer adipiscing elit. Aenean</div>
  <div class="news-item"><b>MAY 19, 2011</b>Lorem ipsum dolor sit ametconsectetuer adipiscing elit. Aenean</div>
  <div class="news-item"><b>MAY 19, 2011</b>Lorem ipsum dolor sit ametconsectetuer adipiscing elit. Aenean</div>
</section>
<div class="more abs">Read more &gt;&gt;</div>

<h2 class="testimonials abs">Testimonials</h2>
<div class="bubble abs">Lorem ipsum dolor sit ametcon-sectetuer adipiscing elit. Aenean commodo ligula egetDolor Aenean massa. Cum &nbsp;eget doloAenean massa. Cum sociis sociis</div>
<svg class="tail abs" width="30" height="22" viewBox="0 0 30 22"><path d="M0 0 L6 20 L24 0 Z" fill="#f4f4f6"/><path d="M0 0 L6 20 L24 0" fill="none" stroke="#ddd"/></svg>
<div class="pager abs" style="left:543px;top:886px">&lt; &gt;</div>
<div class="person abs"><b>Name</b>, webdesigner<br>client@northbeacon.com</div>

<h2 class="newsletter abs">Newsletter</h2>
<div class="email abs">Enter you email</div>
<div class="submit abs">SUBMIT</div>
<h2 class="clients-title abs">Our Clients</h2>
<div class="clients abs">HERE COMES LOGO<br>CLIENTS</div>
<div class="pager abs" style="left:850px;top:933px;color:var(--teal)">&lt; &gt;</div>

<footer class="footer abs">
  <div class="col abs" style="left:56px"><h3>Company</h3><ul><li>Home</li><li>About Us</li><li>Contact Us</li><li>Privacy Policy</li><li>Tearms of use</li></ul></div>
  <div class="col abs" style="left:189px"><h3>Industries</h3><ul><li>Medical / Health Care</li><li>Retail</li><li>Automotive</li><li>Entertainment</li></ul></div>
  <div class="col abs" style="left:362px"><h3>Services</h3><ul><li>Media Planning &amp; Buying C</li><li>Campaign monitoring and reporting</li><li>Commercial Production</li><li>Strategic Planning</li><li>Market Research</li><li>Internet Marketing</li></ul></div>
  <div class="col social abs" style="left:600px"><h3>Follow Us</h3><ul>
    <li>Rss<span style="background:#e8821c"></span></li>
    <li>Buzzline<span style="background:#4fb6d6"></span></li>
    <li>Friendhub<span style="background:#3a5a9a"></span></li></ul></div>
  <div class="col contact abs" style="left:738px"><h3>Contact Us</h3>
    <p>Pixel Harbor, Inc.<br>2240 Harbor Row, Suite 310<br>Bayview, Oregon 97001</p>
    <div class="line"><svg width="14" height="10" viewBox="0 0 14 10"><path d="M1 4 Q7 -1 13 4 L11 5 L9 3 L5 3 L3 5 Z M3 6 H11 V9 H3 Z" fill="#fff"/></svg>555.014.7720 &nbsp;(P)</div>
    <div class="line"><svg width="14" height="12" viewBox="0 0 14 12"><rect x="3" y="0" width="8" height="4" fill="#fff"/><rect x="0" y="4" width="14" height="5" fill="#fff"/><rect x="3" y="8" width="8" height="4" fill="#ccc"/></svg>555.014.7721 &nbsp;(F)</div>
  </div>
</footer>
<div class="copy abs">2011 © &nbsp;pixelharbor.com. All rights reserved.</div>
</body>
</html>
```